Silver Meadow LLC business card

I help with the Marketing and Sales of various Natural, Organic, Eco Friendly and Healthy Main Stream products to Retail Corporate accounts as well as Independents and Distributors.I also highlight Private label items to these same Retail Corporate accounts.Cherish the Moments, Enjoy Life!

Speciality & Health Sales and Marketing

Target Market(s)

Men and Women

Industry/Entity Type

Business

Contact Information for Business Card

Silver Meadow, LLC
Janet Louise Verhagen
438 West Finch Lane
Ste 4-237
Phoenix, AZ 85047
602-555-0147
jverhagen@plumvale.net

Requirements
Must have
• Nice, femine font
Something in the background or on a side with a softness
Nice to have
• Cherish the Moments, Enjoy Life
Should not have
• Hardness

```html
<!DOCTYPE html>
<html lang="en">
<head>
<meta charset="utf-8">
<title>Silver Meadow LLC — Business Card</title>
<link href="https://fonts.googleapis.com/css2?family=Lato:wght@300;400&display=swap" rel="stylesheet">
<style>
  :root {
    --page: #efebe8;
    --front-deep: #3d3440;
    --front-mid: #564a5a;
    --white: #ffffff;
    --blush-white: #f6f0f1;
    --text-dark: #4a3f4c;
    --accent-rose: #c98b9b;
    --foot-mauve: #8f7383;
  }
  * { box-sizing: border-box; margin: 0; padding: 0; }
  html, body { width: 1200px; height: 900px; overflow: hidden; }
  body {
    background: var(--page);
    font-family: "Lato", Arial, sans-serif;
    position: relative;
  }
  .card {
    position: absolute;
    top: 296px;
    width: 540px;
    height: 309px;
    border-radius: 8px;
    overflow: hidden;
    box-shadow: 0 10px 28px rgba(80, 60, 70, 0.16);
  }
  .card--front {
    left: 40px;
    background: radial-gradient(ellipse at 50% 40%, var(--front-mid) 0%, var(--front-deep) 75%);
  }
  .card--back { left: 620px; background: var(--white); }

  .brand {
    position: absolute;
    left: 0; right: 0;
    display: flex;
    flex-direction: column;
    align-items: center;
  }
  .brand__mark {
    width: 52px; height: 52px;
    border-radius: 50%;
    margin-bottom: 12px;
  }
  .brand__name {
    font-weight: 300;
    font-size: 34px;
    letter-spacing: 0.5px;
    white-space: nowrap;
  }
  .card--front .brand { top: 92px; }
  .card--front .brand__mark { background: var(--blush-white); }
  .card--front .brand__name { color: var(--white); }

  .back__top {
    position: absolute; left: 0; top: 0; width: 100%; height: 136px;
    background: radial-gradient(ellipse at 50% 60%, var(--white) 0%, var(--blush-white) 100%);
  }
  .card--back .brand { top: 18px; }
  .card--back .brand__mark { background: var(--accent-rose); width: 46px; height: 46px; margin-bottom: 10px; }
  .card--back .brand__name { color: var(--text-dark); font-size: 30px; }

  .back__band {
    position: absolute; left: 0; top: 136px; width: 100%; height: 145px;
    background: var(--accent-rose);
    color: var(--white);
  }
  .back__foot {
    position: absolute; left: 0; top: 281px; width: 100%; height: 28px;
    background: var(--foot-mauve);
  }
  .person {
    position: absolute; left: 18px; top: 14px; width: 270px;
    text-align: center;
  }
  .person__name { font-size: 21px; font-weight: 400; white-space: nowrap; }
  .person__role { font-size: 14px; font-weight: 300; margin-top: 1px; }
  .person__address { font-size: 15px; font-weight: 300; margin-top: 7px; line-height: 1.3; }
  .contacts {
    position: absolute; left: 300px; top: 22px;
    list-style: none;
    font-size: 14px; font-weight: 300;
  }
  .contacts li { display: flex; align-items: center; height: 24px; white-space: nowrap; }
  .contacts svg { width: 15px; height: 15px; margin-right: 8px; flex: none; }
</style>
</head>
<body>

<section class="card card--front" aria-label="Card front">
  <div class="brand">
    <div class="brand__mark"></div>
    <div class="brand__name">Silver Meadow LLC</div>
  </div>
</section>

<section class="card card--back" aria-label="Card back">
  <div class="back__top"></div>
  <div class="brand">
    <div class="brand__mark"></div>
    <div class="brand__name">Silver Meadow LLC</div>
  </div>

  <div class="back__band">
    <div class="person">
      <p class="person__name">Janet Louise Verhagen</p>
      <p class="person__role">Managing Director</p>
      <p class="person__address">438 West Finch Lane, Ste 4-237<br>Phoenix, AZ 85047</p>
    </div>
    <ul class="contacts">
      <li>
        <svg viewBox="0 0 16 16" aria-hidden="true"><rect width="16" height="16" rx="4" fill="#fff"/><path d="M4 6c0-1.5 8-1.5 8 0v1.2h-2V6.4H6v.8H4z M5 8h6l1 4H4z" fill="#c98b9b"/></svg>
        602-555-0147
      </li>
      <li>
        <svg viewBox="0 0 16 16" aria-hidden="true"><rect width="16" height="16" rx="4" fill="#fff"/><rect x="3" y="4.5" width="10" height="7" rx="1" fill="#c98b9b"/><path d="M3 4.5l5 4 5-4" fill="none" stroke="#fff" stroke-width="1"/></svg>
        jverhagen@plumvale.net
      </li>
      <li>
        <svg viewBox="0 0 16 16" aria-hidden="true"><rect width="16" height="16" rx="4" fill="#fff"/><path d="M6.5 9.5l3-3 M7.5 5l1-1a2 2 0 013 3l-1 1 M8.5 11l-1 1a2 2 0 01-3-3l1-1" fill="none" stroke="#c98b9b" stroke-width="1.5" stroke-linecap="round"/></svg>
        silvermeadow.net
      </li>
    </ul>
  </div>
  <div class="back__foot"></div>
</section>

</body>
</html>
```